Acupuncture business needs business card design

I need a business card for an acupuncture clinic called "Harbourlight Wellness"
It will need the following details:
My name: Marcus Pelling
Acupuncturist
Member TVBH
KWF Treatment Provider
Ph numbers: 581 2734 027 418 5620
Email: marcus@hbwel.example.nz
On the back it will need a table with 2 columns for appointments, one column for time and one for date.

Industry/Entity Type

Clinic

Contact Information for Business Card

Marcus Pelling
Acupuncturist
Member TVBH
KWF Treatment Provider
Email: marcus@hbwel.example.nz

Requirements
Must have
• Marcus Pelling
• Acupuncturist
• Member TVBH
• KWF Treatment Provider
• Ph numbers: 581 2734 027 418 5620
• Email: marcus@hbwel.example.nz
• On the back it will need a table with 2 columns for appointments, one column for time and one for date.

```html
<!DOCTYPE html>
<html lang="en">
<head>
<meta charset="utf-8">
<title>Harbourlight Wellness – Business Card</title>
<link href="https://fonts.googleapis.com/css2?family=Roboto+Condensed:wght@300;400;700&display=swap" rel="stylesheet">
<style>
  :root {
    --teal: #1e7f96;
    --teal-dark: #176a7e;
    --sky: #29a9d6;
    --sky-light: #8fd3ec;
    --ink: #2f3338;
    --paper: #ffffff;
    --stage: #e9ecee;
  }
  * { box-sizing: border-box; margin: 0; padding: 0; }
  html, body {
    width: 1200px; height: 948px; overflow: hidden;
    background: var(--stage);
    font-family: "Roboto Condensed", Arial, sans-serif;
  }
  .sheet {
    width: 1200px; height: 948px;
    display: flex; align-items: center; justify-content: center; gap: 50px;
  }
  .card {
    position: relative; width: 525px; height: 300px; overflow: hidden;
    box-shadow: 0 6px 18px rgba(0,0,0,.18);
  }

  /* Front */
  .card-front { background: var(--paper); color: var(--ink); }
  .brand { position: absolute; left: 24px; top: 22px; display: flex; align-items: center; gap: 10px; }
  .brand-dot { width: 30px; height: 30px; border-radius: 50%; background: var(--sky); flex: none; }
  .brand-name { font-size: 29px; font-weight: 700; color: var(--sky); line-height: 1; }
  .brand-tagline {
    position: absolute; left: 64px; top: 56px;
    font-size: 10.5px; letter-spacing: 3.2px; color: var(--sky); text-transform: uppercase;
  }
  .address { position: absolute; left: 40px; top: 98px; font-size: 13px; line-height: 22px; }
  .contact { position: absolute; left: 248px; top: 98px; font-size: 13px; line-height: 22px; list-style: none; }
  .contact li { display: flex; align-items: center; gap: 8px; }
  .contact svg { width: 13px; height: 13px; flex: none; }
  .wave { position: absolute; inset: 0; width: 100%; height: 100%; }
  .practitioner { position: absolute; left: 24px; top: 206px; color: var(--paper); }
  .practitioner-name { font-size: 17px; font-weight: 700; line-height: 22px; }
  .practitioner-role { font-size: 11.5px; line-height: 16px; font-weight: 300; }

  /* Back */
  .card-back { background: var(--teal); color: var(--paper); }
  .appointments {
    position: absolute; left: 40px; top: 38px; width: 360px;
    border-collapse: separate; border-spacing: 14px 12px;
  }
  .appointments th {
    font-size: 14px; font-weight: 400; text-align: left; padding: 0 0 0 2px; letter-spacing: .5px;
  }
  .appointments td { height: 16px; background: rgba(255,255,255,.82); }
  .website {
    position: absolute; left: 0; right: 0; bottom: 30px; text-align: center;
    font-size: 15px; letter-spacing: 3px;
  }
</style>
</head>
<body>
<main class="sheet">

  <section class="card card-front" aria-label="Business card front">
    <svg class="wave" viewBox="0 0 525 300" preserveAspectRatio="none" aria-hidden="true">
      <path d="M0,132 C140,170 230,250 525,262" fill="none" stroke="var(--sky-light)" stroke-width="5"/>
      <path d="M0,148 C150,185 240,262 525,276 L525,300 L0,300 Z" fill="var(--teal)"/>
      <path d="M0,158 C150,195 240,270 525,284" fill="none" stroke="var(--sky)" stroke-width="3"/>
    </svg>

    <div class="brand">
      <span class="brand-dot"></span>
      <span class="brand-name">Harbourlight Wellness</span>
    </div>
    <p class="brand-tagline">Acupuncture Physiotherapy</p>

    <address class="address">
      Street Name, City Name<br>
      Zipcode-01234
    </address>

    <ul class="contact">
      <li>
        <svg viewBox="0 0 16 16" aria-hidden="true"><path fill="var(--teal)" d="M3.6 1.2l2.3 2.6-1.3 1.9c.9 2.1 2.5 3.7 4.6 4.7l1.9-1.3 2.6 2.3-1.4 2.5C6.8 13.6 2.4 9.2 1.1 2.6z"/></svg>
        581-2734 · 027-418-5620
      </li>
      <li>
        <svg viewBox="0 0 16 16" aria-hidden="true"><rect x="1" y="3" width="14" height="10" rx="1.5" fill="var(--teal)"/><path d="M1.5 4l6.5 5 6.5-5" fill="none" stroke="#fff" stroke-width="1.3"/></svg>
        marcus@hbwel.example.nz
      </li>
    </ul>

    <div class="practitioner">
      <p class="practitioner-name">Marcus Pelling</p>
      <p class="practitioner-role">Acupuncturist, Member TVBH</p>
      <p class="practitioner-role">KWF Treatment Provider</p>
    </div>
  </section>

  <section class="card card-back" aria-label="Business card back">
    <table class="appointments">
      <thead>
        <tr><th>Date</th><th>Time</th></tr>
      </thead>
      <tbody>
        <tr><td></td><td></td></tr>
        <tr><td></td><td></td></tr>
        <tr><td></td><td></td></tr>
        <tr><td></td><td></td></tr>
      </tbody>
    </table>
    <p class="website">www.hbwel.example.nz</p>
  </section>

</main>
</body>
</html>
```